Defense Attorney Business Card Design Project/ Stationary

I am looking for a distinctive business card design for my solo law practice.
I practice criminal defense, both juvenile and adult, including DUI. I am a very experienced attorney with prior military experience. The design should convey a traditional, old school flair, but not be too stodgy or uptight. Some color. My logo should appear.
Updates

Project Deadline Extended Reason: I misunderstood how this project works and I was not prepared with my logo when this project ran the first time. Added Thursday, November 13, 2014

Project Deadline Extended
Reason: I was sent overseas on military duty last year, which interrupted this project. Thank you for your participation... I hope we can get this done this week! Thank you, Neil

Target Market(s)

Regular everyday people looking for strong, knowledgeable, authoritative representation while they are faced with criminal charges. Many have never been charged with a crime before. A reassuring air is therefore desired.

Industry/Entity Type

Business

Contact Information for Business Card

My information is:
Theodore M. Quill, Attorney at Law
785 Birch Avenue Suite 300
Oakland, California 94719
Tel: (510) 384-6125
Fax: (510) 391-7802
email: neilquilllaw@mailvine.example
web: www.neilquilllaw.example

Font styles to use
Serif
Sans Serif
Decorative

Colors
0255a3
ffffff

Requirements
Must have
• Sharp lines, bold elements. Conservative use of colors, such as deep blues, burgundy, grays for example.
• While my logo says "Theodore M. Quill", it should be modified to show "Theodore M. Quill".
Should not have
• Cliche imagery such as scales of justice, gavels, Statue of Liberty, etc.

```html
<!DOCTYPE html>
<html lang="en">
<head>
<meta charset="UTF-8">
<title>Theodore M. Quill – Business Card</title>
<link rel="stylesheet" href="https://fonts.googleapis.com/css2?family=Jura:wght@500;600;700&display=swap">
<style>
  :root {
    --stage: #2a2b2d;
    --navy: #0e3d55;
    --silver-light: #fbfbfc;
    --silver-mid: #e6e8ea;
    --silver-dark: #cdd0d3;
    --ink: #4a4d52;
    --white: #ffffff;
  }
  * { margin: 0; padding: 0; box-sizing: border-box; }
  html, body {
    width: 1200px; height: 870px; overflow: hidden;
    background: var(--stage);
    font-family: "Jura", sans-serif;
  }
  .canvas { position: relative; width: 1200px; height: 870px; }

  .card {
    position: absolute;
    background: linear-gradient(160deg, var(--silver-light) 0%, var(--silver-mid) 55%, var(--silver-dark) 100%);
    box-shadow: 0 10px 30px rgba(0,0,0,.45);
    overflow: hidden;
  }

  /* Back of card */
  .card-back { left: 70px; top: 60px; width: 580px; height: 330px; }
  .back-mark {
    position: absolute; inset: 0;
    display: flex; align-items: center; justify-content: center; gap: 16px;
    white-space: nowrap;
  }
  .back-mark .dot {
    width: 40px; height: 40px; border-radius: 50%; background: var(--navy); flex: none;
  }
  .back-mark .mark-name {
    color: var(--navy); font-weight: 700; font-size: 42px; letter-spacing: 1px;
  }

  /* Front of card */
  .card-front { left: 450px; top: 420px; width: 700px; height: 400px; }
  .front-band {
    position: absolute; left: 0; right: 0; bottom: 0; height: 178px;
    background: var(--navy);
  }
  .contact-list {
    position: absolute; left: 38px; top: 34px;
    list-style: none;
  }
  .contact-list li {
    display: flex; align-items: center; gap: 10px;
    font-size: 15px; font-weight: 600; color: var(--ink);
    height: 27px; white-space: nowrap;
  }
  .contact-list svg { width: 15px; height: 15px; fill: var(--ink); flex: none; }

  .brand {
    position: absolute; right: 38px; top: 112px; text-align: center;
    color: var(--navy); font-weight: 700; white-space: nowrap;
  }
  .brand .brand-name { font-size: 30px; letter-spacing: .5px; line-height: 1; }
  .brand .brand-tag {
    margin-top: 6px; padding-top: 5px; border-top: 1.5px solid var(--navy);
    font-size: 13px; letter-spacing: 3px; text-transform: uppercase;
  }

  .address {
    position: absolute; left: 38px; top: 252px;
    color: var(--white); font-size: 19px; font-weight: 600; line-height: 1.35;
  }
  .person {
    position: absolute; right: 38px; bottom: 30px; text-align: right; color: var(--white);
  }
  .person .person-name { font-size: 24px; font-weight: 700; letter-spacing: 1px; text-transform: uppercase; }
  .person .person-title { font-size: 17px; font-weight: 600; margin-top: 2px; }
</style>
</head>
<body>
<main class="canvas">

  <section class="card card-back" aria-label="Card back">
    <div class="back-mark">
      <span class="dot"></span>
      <span class="mark-name">Theodore M. Quill</span>
    </div>
  </section>

  <section class="card card-front" aria-label="Card front">
    <ul class="contact-list">
      <li>
        <svg viewBox="0 0 24 24" aria-hidden="true"><path d="M6.6 10.8a15 15 0 0 0 6.6 6.6l2.2-2.2c.3-.3.7-.4 1-.2 1.1.4 2.3.6 3.6.6.6 0 1 .4 1 1V20c0 .6-.4 1-1 1A17 17 0 0 1 3 4c0-.6.4-1 1-1h3.5c.6 0 1 .4 1 1 0 1.3.2 2.5.6 3.6.1.3 0 .7-.2 1z"/></svg>
        (510) 384-6125
      </li>
      <li>
        <svg viewBox="0 0 24 24" aria-hidden="true"><path d="M7 1h10a2 2 0 0 1 2 2v18a2 2 0 0 1-2 2H7a2 2 0 0 1-2-2V3a2 2 0 0 1 2-2zm0 3v14h10V4zm5 15.5a1 1 0 1 0 0 2 1 1 0 0 0 0-2z"/></svg>
        (510) 384-6125
      </li>
      <li>
        <svg viewBox="0 0 24 24" aria-hidden="true"><path d="M6 2h9l3 3v4h2a2 2 0 0 1 2 2v9a2 2 0 0 1-2 2H4a2 2 0 0 1-2-2v-9a2 2 0 0 1 2-2h2zm2 2v5h8V6h-2V4zm-2 9v2h12v-2z"/></svg>
        (510) 391-7802
      </li>
      <li>
        <svg viewBox="0 0 24 24" aria-hidden="true"><path d="M2 5h20v14H2zm2 2v.5l8 5 8-5V7zm0 2.9V17h16V9.9l-8 5z"/></svg>
        neilquilllaw@mailvine.example
      </li>
      <li>
        <svg viewBox="0 0 24 24" aria-hidden="true"><path d="M12 2a10 10 0 1 0 0 20 10 10 0 0 0 0-20zm0 2c.9 0 2.1 1.6 2.7 4H9.3C9.9 5.6 11.1 4 12 4zM4.3 10h4.6a18 18 0 0 0 0 4H4.3a8 8 0 0 1 0-4zm6.6 0h2.2a16 16 0 0 1 0 4h-2.2a16 16 0 0 1 0-4zm4.2 0h4.6a8 8 0 0 1 0 4h-4.6a18 18 0 0 0 0-4zM9.3 16h5.4c-.6 2.4-1.8 4-2.7 4s-2.1-1.6-2.7-4z"/></svg>
        www.neilquilllaw.example
      </li>
    </ul>

    <div class="brand">
      <div class="brand-name">Theodore M. Quill</div>
      <div class="brand-tag">Attorney at Law</div>
    </div>

    <div class="front-band"></div>

    <p class="address">785 Birch Avenue Suite 300<br>Oakland, CA 94719</p>

    <div class="person">
      <div class="person-name">Theodore M. Quill</div>
      <div class="person-title">Criminal Defense</div>
    </div>
  </section>

</main>
</body>
</html>
```